2 banners on the outside wall of the hall

Banner 1:
KalviMar specializes in the planning, construction, and maintenance of high-quality pond systems, particularly swimming ponds, natural pools, garden ponds, koi ponds, streams, and waterfalls. Learn more at www.kalvimar.de
The following data should be included:
Planning and construction of swimming ponds and natural pools, as well as garden ponds and koi ponds
100% organic
Individually planned
Over 20 years of experience
04627 3150962
www.kalvimar.de
“Logo-KalviMar”
Banner 2:
Grünflut-Laden is the online shop for high-quality aquatic plants for ponds and aquariums.
More information at https://gruenflut-laden.de
Online shop for pond plants and water lilies, as well as aquarium plants and accessories
Over 400 plant species
Top gardener quality
Secure packaging & fast shipping
04627 3150961
www.gruenflut-laden. de
“Logo Greenflow shop”
Here's roughly what we envision:
The designs for each banner should be clearly visible and include everything needed, without appearing cluttered. In other words, it should be immediately clear what the banner is about.
We should also be made aware of our unique selling points and advantages.
It is important that the banners also harmonize visually with each other.
We liked the banner image in the attachment and it serves as inspiration.
The banner print data is produced as follows:
• Banner size: Width x Height: 3880 mm x 1880 mm
• Material: Mesh banner, PVFormat: PDF (X-3:2000)
• Fonts: converted into paths
• Trim allowance: +2 mm all around
• Color space: CMYK
• Resolution: 72 dpi (recommended) at 1:1 resolution
Look and feel
Each slider illustrates characteristics of the customer's brand and the style your logo design should communicate.

```html
<!DOCTYPE html>
<html lang="de">
<head>
<meta charset="utf-8">
<title>KalviMar &amp; Grünflut-Laden – Hallenbanner</title>
<link href="https://fonts.googleapis.com/css2?family=Baloo+2:wght@700;800&display=swap" rel="stylesheet">
<style>
  :root {
    --mint: #e8f2ec;
    --navy: #2a5a85;
    --lime: #8dc63f;
    --leaf: #2e9a48;
    --forest: #3d8a55;
    --white: #ffffff;
  }
  * { margin: 0; padding: 0; box-sizing: border-box; }
  html, body { width: 1200px; height: 1200px; overflow: hidden; background: var(--white); }
  body { position: relative; font-family: "Baloo 2", "Arial Black", sans-serif; font-weight: 800; }
  .banner { position: absolute; left: 0; width: 1200px; height: 582px; background: var(--mint); overflow: hidden; }
  .banner--pond { top: 0; }
  .banner--plants { top: 618px; }
  .corner { position: absolute; right: 0; top: 0; width: 60px; height: 110px; }
  .headline { position: absolute; left: 30px; color: var(--navy); font-size: 40px; line-height: 43px; text-transform: uppercase; font-weight: 800; white-space: nowrap; }
  .banner--pond .headline { top: 74px; }
  .banner--plants .headline { top: 94px; }
  .banner--pond .accent { color: var(--lime); }
  .banner--plants .accent { color: var(--leaf); }
  .usp { position: absolute; left: 23px; height: 51px; border-radius: 7px; color: var(--white); font-size: 24px; display: flex; align-items: center; padding: 3px 0 0 6px; text-transform: uppercase; white-space: nowrap; }
  .banner--pond .usp { background: var(--lime); }
  .banner--plants .usp { background: var(--leaf); }
  .contact { position: absolute; left: 29px; height: 32px; border-radius: 7px; background: var(--navy); color: var(--lime); font-size: 20px; display: flex; align-items: center; padding: 3px 0 0 37px; white-space: nowrap; }
  .contact svg { position: absolute; left: 3px; top: 3px; width: 26px; height: 26px; }
  .brand { position: absolute; color: var(--navy); line-height: 1; white-space: nowrap; font-weight: 800; }
  .photo { position: absolute; right: 0; top: 168px; width: 540px; height: 414px; }
</style>
</head>
<body>

<section class="banner banner--pond">
  <svg class="corner" viewBox="0 0 60 110" aria-hidden="true"><path d="M10,0 C20,30 0,55 20,80 C32,96 50,100 60,108 L60,0 Z" fill="var(--forest)"/></svg>

  <h1 class="headline">
    Planung und Bau von<br>
    <span class="accent">Schwimmteichen</span> und<br>
    <span class="accent">Naturpools</span> sowie Gartenteichen<br>
    und Koiteichen
  </h1>

  <div class="usp" style="top:251px;width:238px">100% biologisch</div>
  <div class="usp" style="top:315px;width:281px">Individuell geplant</div>
  <div class="usp" style="top:378px;width:354px">Über 20 Jahre Erfahrung</div>

  <div class="contact" style="top:488px;width:222px">
    <svg viewBox="0 0 26 26" aria-hidden="true"><circle cx="13" cy="13" r="12" fill="var(--white)"/><path d="M8.5,7 l2.5,-0.5 1.5,3.5 -1.8,1.2 c0.8,1.8 2,3 3.6,3.8 l1.2,-1.8 3.5,1.5 -0.5,2.5 c-6,0.5 -10.5,-4 -10,-10.2z" fill="var(--forest)"/></svg>
    04627 3150962
  </div>
  <div class="contact" style="top:532px;width:222px">
    <svg viewBox="0 0 26 26" aria-hidden="true"><circle cx="13" cy="13" r="12" fill="var(--forest)"/><g fill="none" stroke="var(--white)" stroke-width="1.2"><circle cx="13" cy="13" r="7.5"/><ellipse cx="13" cy="13" rx="3.3" ry="7.5"/><path d="M5.5,13 h15 M7,9 h12 M7,17 h12"/></g></svg>
    www.kalvimar.de
  </div>

  <div class="brand" style="left:770px;top:60px;font-size:72px">KalviMar</div>

  <svg class="photo" viewBox="0 0 540 414" role="img" aria-label="Foto eines Naturpools mit Holzdeck, grünem Wasser und bepflanztem Garten">
    <defs><linearGradient id="poolTone" x1="0" y1="0" x2="0" y2="1"><stop offset="0" stop-color="#6f8f5a"/><stop offset="0.45" stop-color="#4f7a46"/><stop offset="0.7" stop-color="#3fb58a"/><stop offset="1" stop-color="#b59a72"/></linearGradient></defs>
    <path d="M0,200 C0,140 50,118 105,112 C165,106 170,48 245,24 C315,2 355,62 400,42 C450,18 480,0 540,8 L540,414 L12,414 C6,362 28,332 38,302 C48,262 0,252 0,200 Z" fill="url(#poolTone)"/>
  </svg>
</section>

<section class="banner banner--plants">
  <svg class="corner" viewBox="0 0 60 110" aria-hidden="true"><path d="M10,0 C20,30 0,55 20,80 C32,96 50,100 60,108 L60,0 Z" fill="var(--forest)"/></svg>

  <h2 class="headline">
    Online-Shop für <span class="accent">Teichpflanzen</span><br>
    und <span class="accent">Seerosen</span>, sowie<br>
    Aquarienpflanzen und Zubehör
  </h2>

  <div class="usp" style="top:253px;width:340px">Über 400 Pflanzenarten</div>
  <div class="usp" style="top:315px;width:338px">Top-Gärtner-Qualität</div>
  <div class="usp" style="top:379px;width:563px">Sichere Verpackung &amp; schneller Versand</div>

  <div class="contact" style="top:491px;width:222px">
    <svg viewBox="0 0 26 26" aria-hidden="true"><circle cx="13" cy="13" r="12" fill="var(--white)"/><path d="M8.5,7 l2.5,-0.5 1.5,3.5 -1.8,1.2 c0.8,1.8 2,3 3.6,3.8 l1.2,-1.8 3.5,1.5 -0.5,2.5 c-6,0.5 -10.5,-4 -10,-10.2z" fill="var(--forest)"/></svg>
    04627 3150961
  </div>
  <div class="contact" style="top:531px;width:290px">
    <svg viewBox="0 0 26 26" aria-hidden="true"><circle cx="13" cy="13" r="12" fill="var(--forest)"/><g fill="none" stroke="var(--white)" stroke-width="1.2"><circle cx="13" cy="13" r="7.5"/><ellipse cx="13" cy="13" rx="3.3" ry="7.5"/><path d="M5.5,13 h15 M7,9 h12 M7,17 h12"/></g></svg>
    www.gruenflut-laden.de
  </div>

  <div class="brand" style="left:690px;top:56px;font-size:56px">Grünflut-Laden</div>

  <svg class="photo" viewBox="0 0 540 414" role="img" aria-label="Foto eines Gartenteichs mit Seerosen, Schilf und Steinen am Ufer">
    <defs><linearGradient id="pondTone" x1="0" y1="0" x2="0" y2="1"><stop offset="0" stop-color="#7da64a"/><stop offset="0.3" stop-color="#2c3b2a"/><stop offset="0.6" stop-color="#5f8f3c"/><stop offset="1" stop-color="#6e8a4e"/></linearGradient></defs>
    <path d="M0,200 C0,140 50,118 105,112 C165,106 170,48 245,24 C315,2 355,62 400,42 C450,18 480,0 540,8 L540,414 L12,414 C6,362 28,332 38,302 C48,262 0,252 0,200 Z" fill="url(#pondTone)"/>
  </svg>
</section>

</body>
</html>
```